Health and Fitness Club requires a stunning and simple website

We are a health and fitness club based in Dubai, when we launch we will be the biggest club in the country, we will also have the 2 largest activity rooms in the country, we are setting a new standard in the industry by offering one thing, our attitude.

Our attitude means the following:
unlike other clubs we have no hidden charges or fees
our members can join daily, monthly, 6 months or annually
our service and facility are comparable to 5* hotel gyms
our equipment is second to none
our space is the biggest in the country
we do not force our members to use our in-house personal trainers - you can bring your own and we will not charge them entry!
we will have a cutting edge brawnmesh box in our gym with classes by the best trainers in the country
we will be providing free-lance personal trainers a platform to engage customers, grow their business and even use our activity rooms for classes

Basically we will be a gym like no other, simply because we are gym people and we hate the restrictive practices and hidden charges by other gyms, so we are making our own gym which focuses on quality and service.

All of this has to be communicated in the style of the website, the colors of the website we want to be limited to the logo colors as this will be the same theme running throughout the gym.

The landing page of the website HAS to incorporate elements from our social media presences, this basically is the usual, chirplo, snapvault, kinwall. We can have these as a sidebar, the centre of the page should display the latest article from our blog (also on the website) Also we need to have a calendar for activities and classes on the front page. The menu should have links to the following:
Latest News
About us
Team
Gallery
Membership
Classes
Member Log In
Contact Us
Location

The style of the website has to be similar to the logo, particularly in terms of the fonts used.

```html
<!DOCTYPE html>
<html lang="en">
<head>
<meta charset="utf-8">
<title>Ironhouse Health and Fitness</title>
<link href="https://fonts.googleapis.com/css2?family=Oswald:wght@400;500;700&family=Arimo:wght@400;700&display=swap" rel="stylesheet">
<style>
:root{
  --red:#c9141c;
  --red-dark:#a50e15;
  --ink:#1a1a1a;
  --grey:#666;
  --light:#999;
  --line:#d9d9d9;
  --footer:#140909;
  --white:#fff;
}
*{margin:0;padding:0;box-sizing:border-box}
html,body{width:732px;height:1200px;overflow:hidden;background:var(--white)}
body{position:relative;font-family:'Arimo',Arial,sans-serif;color:var(--ink)}
.abs{position:absolute}
.cond{font-family:'Oswald','Arial Narrow',sans-serif}

/* header */
.brand{left:80px;top:12px;display:flex;align-items:center;gap:6px}
.brand-dot{width:40px;height:40px;border-radius:50%;background:var(--red)}
.brand-name{font-family:'Oswald',sans-serif;font-weight:700;font-size:13px;color:var(--ink);letter-spacing:.5px}
.call{left:386px;top:12px}
.call-label,.hours-label{font-family:'Oswald',sans-serif;font-size:14px;color:#9a9a9a;display:flex;align-items:center;gap:5px}
.call-num{font-family:'Oswald',sans-serif;font-size:15px;color:#444;margin-top:6px}
.hours{left:521px;top:10px}
.hours-label small{font-size:10px}
.search{left:515px;top:38px;width:137px;height:20px;border:1px solid var(--line);display:flex;align-items:center}
.search span{font-size:7px;color:#bbb;padding-left:5px;flex:1}
.search i{width:16px;height:16px;border-radius:50%;background:var(--red);margin-right:2px;display:flex;align-items:center;justify-content:center}

.nav{left:0;top:69px;width:732px;height:29px;background:linear-gradient(#d21d24,var(--red-dark))}
.nav ul{list-style:none;display:flex;justify-content:space-between;padding:0 80px 0 81px;height:100%;align-items:center}
.nav li{font-family:'Oswald',sans-serif;font-size:10.5px;color:var(--white)}

/* hero */
.hero{left:0;top:98px;width:732px;height:312px;background:linear-gradient(100deg,#8c8c8c 0%,#cfcfcf 35%,#e7e7e7 55%,#6a6a8a 75%,#d8d8d8 100%)}
.hero-rule{left:80px;top:173px;width:252px;height:1px;background:var(--white)}
.hero-title{left:78px;top:175px;font-family:'Oswald',sans-serif;font-weight:700;font-size:33px;color:var(--white);letter-spacing:-.5px}
.hero-text{left:80px;top:235px;width:270px;font-family:'Oswald',sans-serif;font-weight:400;font-size:10.5px;line-height:15px;color:var(--white)}
.hero-btn{left:80px;top:279px;width:87px;height:30px;border:2px solid var(--white);font-family:'Oswald',sans-serif;font-size:12px;color:var(--white);display:flex;align-items:center;justify-content:center}
.arrow{width:26px;height:26px;border-radius:50%;border:2px solid var(--white);display:flex;align-items:center;justify-content:center;background:rgba(0,0,0,.25)}
.social-side{left:698px;top:112px;display:flex;flex-direction:column;gap:6px}
.social-side span{width:27px;height:27px;border-radius:50%}

/* sections */
.sec-title{font-family:'Oswald',sans-serif;font-weight:700;font-size:17px;color:var(--red);letter-spacing:-.3px}
.pager{display:flex;gap:2px}
.pager svg{display:block}

.card{width:130px}
.card-img{height:100px}
.card-label{height:24px;background:var(--ink);color:var(--white);font-family:'Oswald',sans-serif;font-size:12.5px;display:flex;align-items:center;justify-content:center}
.card-text{font-family:'Oswald',sans-serif;font-weight:400;font-size:7px;color:#888;line-height:17.5px;margin-top:3px}
.card-text em{font-style:normal;color:var(--red);float:right}

.article{left:82px;top:692px;width:374px;height:138px;border:1px solid var(--line);padding:2px;display:flex}
.article-red{width:57px;background:var(--red);display:flex;align-items:center;justify-content:center}
.date{width:42px;height:42px;border-radius:50%;background:var(--white);border:3px solid var(--ink);display:flex;flex-direction:column;align-items:center;justify-content:center;font-family:'Oswald',sans-serif;font-weight:700;line-height:1}
.date b{font-size:15px}.date small{font-size:6px}
.article-img{flex:1;background:linear-gradient(90deg,#3c3f46,#6b6e76 40%,#c43a3a 80%,#e9e9e9)}
.article-title{left:143px;top:846px;font-family:'Oswald',sans-serif;font-size:10.5px}
.article-body{left:143px;top:868px;width:320px;font-size:7.2px;line-height:15.5px;color:#555}
.btn-dark{left:143px;top:950px;width:66px;height:19px;background:var(--ink);color:var(--white);font-family:'Oswald',sans-serif;font-size:9px;display:flex;align-items:center;justify-content:center}

.calendar{left:488px;top:691px;width:164px;height:151px;border:2px solid #b7b7b7;padding:6px 9px}
.cal-head{display:flex;justify-content:space-between;font-size:10px;color:#555;padding:0 4px;letter-spacing:.5px}
.cal-head span:first-child,.cal-head span:last-child{color:#999;font-size:8px}
.cal-grid{display:grid;grid-template-columns:repeat(7,17px);gap:3px 3px;margin-top:8px;justify-content:center}
.cal-grid div{height:13px;font-size:8px;display:flex;align-items:center;justify-content:center;border:1px solid #e3e3e3;color:#555}
.cal-grid .dow{border:none;color:#888;font-weight:700}
.cal-grid .mute{color:#ccc}
.cal-grid .now{background:#666;color:var(--white);border-color:#666}
.cal-grid .bold{font-weight:700;color:#222}

.activity{left:488px;top:858px;width:164px;display:flex;gap:7px}
.activity-img{width:65px;height:55px;background:linear-gradient(135deg,#e9e4df,#b7c4cc 60%,#8aa0aa)}
.activity-date{font-family:'Oswald',sans-serif;font-size:7px;color:var(--red)}
.activity-text{font-size:6.5px;line-height:13px;color:#666;text-align:justify}
.divider{height:1px;background:var(--line);width:164px;left:488px}
.cardio-title{left:488px;top:935px;font-family:'Oswald',sans-serif;font-size:11px;color:var(--red)}
.cardio-sub{left:488px;top:950px;font-size:6.5px;color:#666}

/* footer */
.footer{left:0;top:1004px;width:732px;height:196px;background:var(--footer)}
.f-title{font-size:10.5px;color:var(--white)}
.thumbs{left:80px;top:1052px;display:grid;grid-template-columns:repeat(3,38px);gap:4px 4px}
.thumbs span{height:38px;background:linear-gradient(135deg,#c8c0bb,#7e8fa1 60%,#b7392f)}
.f-list{font-size:7px;line-height:10px;color:#ddd}
.f-item{display:flex;gap:6px;margin-bottom:10px}
.f-item i{width:8px;height:8px;border-radius:50%;background:var(--white);flex:none;margin-top:1px}
.email{left:543px;top:1054px;width:109px;height:14px;background:var(--white);font-size:6px;color:#999;padding:3px 3px}
.subscribe{left:596px;top:1078px;width:56px;height:16px;background:var(--red);color:var(--white);font-family:'Oswald',sans-serif;font-size:8px;display:flex;align-items:center;justify-content:center}
.f-social{left:540px;top:1113px;display:flex;gap:5px}
.f-social span{width:19px;height:19px}
.copy{left:0;top:1169px;width:732px;text-align:center;font-size:7px;color:#eee}
</style>
</head>
<body>

<header>
  <div class="abs brand">
    <span class="brand-dot"></span>
    <span class="brand-name">IRONHOUSE</span>
  </div>
  <div class="abs call">
    <div class="call-label">
      <svg width="16" height="16" viewBox="0 0 16 16"><circle cx="8" cy="8" r="7" fill="none" stroke="#aaa" stroke-width="1.3"/><path d="M5.5 4.5l1.5 0 .6 1.8-1 .8a5 5 0 0 0 2.3 2.3l.8-1 1.8.6v1.5c-3.2.4-6.4-2.8-6-6z" fill="#aaa"/></svg>
      Call Now
    </div>
    <div class="call-num">1-555-010-4477</div>
  </div>
  <div class="abs hours">
    <div class="hours-label">
      <svg width="15" height="15" viewBox="0 0 16 16"><circle cx="8" cy="8" r="7" fill="none" stroke="#aaa" stroke-width="1.5"/><path d="M8 4v4h3" stroke="#aaa" stroke-width="1.5" fill="none"/></svg>
      Opening Hours <small>(mon to sat)</small>
    </div>
  </div>
  <div class="abs search">
    <span>Enter any Keywords...</span>
    <i><svg width="9" height="9" viewBox="0 0 10 10"><circle cx="4" cy="4" r="2.8" fill="none" stroke="#fff" stroke-width="1.3"/><path d="M6 6l3 3" stroke="#fff" stroke-width="1.4"/></svg></i>
  </div>
</header>

<nav class="abs nav">
  <ul>
    <li>About us</li><li>Team</li><li>Gallery</li><li>Membership</li><li>Classes</li><li>Latest News</li><li>Member Log In</li><li>Contact Us</li><li>Location</li>
  </ul>
</nav>

<section>
  <div class="abs hero" role="img" aria-label="Woman training on a leg press machine in a bright gym"></div>
  <div class="abs hero-rule"></div>
  <h1 class="abs hero-title">HEALTH AND FITNESS</h1>
  <p class="abs hero-text">We are a health and fitness club based in Dubai, when we launch we will be the biggest club in the country.....................</p>
  <div class="abs hero-btn">MORE DETAILS</div>
  <div class="abs arrow" style="left:4px;top:242px"><svg width="10" height="10" viewBox="0 0 10 10"><path d="M6.5 1.5L3 5l3.5 3.5" stroke="#fff" stroke-width="1.6" fill="none"/></svg></div>
  <div class="abs arrow" style="left:702px;top:242px"><svg width="10" height="10" viewBox="0 0 10 10"><path d="M3.5 1.5L7 5 3.5 8.5" stroke="#fff" stroke-width="1.6" fill="none"/></svg></div>
  <div class="abs social-side">
    <span style="background:#3c7be0" aria-label="kinwall"></span>
    <span style="background:#1db4ea" aria-label="chirplo"></span>
    <span style="background:#f07a16" aria-label="snapvault"></span>
  </div>
</section>

<section>
  <h2 class="abs sec-title" style="left:79px;top:424px">CLASSES</h2>
  <div class="abs pager" style="left:619px;top:428px">
    <svg width="16" height="16" viewBox="0 0 16 16"><circle cx="8" cy="8" r="7" fill="none" stroke="#111" stroke-width="1.6"/><path d="M9.5 4.5L6 8l3.5 3.5" stroke="#111" stroke-width="1.8" fill="none"/></svg>
    <svg width="16" height="16" viewBox="0 0 16 16"><circle cx="8" cy="8" r="7" fill="none" stroke="#111" stroke-width="1.6"/><path d="M6.5 4.5L10 8l-3.5 3.5" stroke="#111" stroke-width="1.8" fill="none"/></svg>
  </div>

  <div class="abs card" style="left:80px;top:460px">
    <div class="card-img" role="img" aria-label="Group doing sit-ups on exercise balls" style="background:linear-gradient(135deg,#d8d2e8,#6a7fc0 55%,#e6b8c6)"></div>
    <div class="card-label">GROUP CLASSES</div>
    <p class="card-text">we are gym people and we hate the restrictive practices and hidden.................. <em>Read More</em></p>
  </div>
  <div class="abs card" style="left:227px;top:460px">
    <div class="card-img" role="img" aria-label="Three women in a yoga lunge pose" style="background:linear-gradient(180deg,#f2f2f2,#c9c9c9 60%,#4a4a4a)"></div>
    <div class="card-label">LEARN YOGA</div>
    <p class="card-text">we are gym people and we hate the restrictive practices and hidden.................. <em>Read More</em></p>
  </div>
  <div class="abs card" style="left:375px;top:460px">
    <div class="card-img" role="img" aria-label="Partner yoga pose on a beach" style="background:linear-gradient(180deg,#d9e3ea,#a7bac6 55%,#d2c2a6)"></div>
    <div class="card-label">PERSONAL TRAINING</div>
    <p class="card-text">we are gym people and we hate the restrictive practices and hidden.................. <em>Read More</em></p>
  </div>
  <div class="abs card" style="left:521px;top:460px">
    <div class="card-img" role="img" aria-label="Martial arts class in a dojo" style="background:linear-gradient(180deg,#8d5a6f,#c9c9cf 55%,#7a3b48)"></div>
    <div class="card-label">MARTIAL ART LESSONS</div>
    <p class="card-text">we are gym people and we hate the restrictive practices and hidden.................. <em>Read More</em></p>
  </div>
</section>

<section>
  <h2 class="abs sec-title" style="left:79px;top:655px">THE LATEST ARTICLE</h2>
  <div class="abs pager" style="left:424px;top:659px">
    <svg width="16" height="16" viewBox="0 0 16 16"><circle cx="8" cy="8" r="7" fill="none" stroke="#111" stroke-width="1.6"/><path d="M9.5 4.5L6 8l3.5 3.5" stroke="#111" stroke-width="1.8" fill="none"/></svg>
    <svg width="16" height="16" viewBox="0 0 16 16"><circle cx="8" cy="8" r="7" fill="none" stroke="#111" stroke-width="1.6"/><path d="M6.5 4.5L10 8l-3.5 3.5" stroke="#111" stroke-width="1.8" fill="none"/></svg>
  </div>
  <div class="abs article">
    <div class="article-red"><div class="date"><b>20</b><small>JAN</small></div></div>
    <div class="article-img" role="img" aria-label="Man lifting a dumbbell in a red vest"></div>
  </div>
  <h3 class="abs article-title">How to purchase and care for a yoga mat.</h3>
  <p class="abs article-body">Lorem ipsum dolor sit amet, consectetur adipisicing elit. Dicta ducimus numquam quae vo dignissimos, earum iste maxime nam omnis saepe similique! A ad numquam reprehender incidunt inventore necessitatibus odio saepe. Lorem ipsum dolor sit amet, consectetur ad Accusantium ad alias, aliquid aut corporis distinctio dolore eaque esse harum in ipsam nam nihil obcaecati odit omnis reiciendis sed..........................</p>
  <div class="abs btn-dark">Read More</div>
</section>

<aside>
  <h2 class="abs sec-title" style="left:487px;top:655px">RECENT ACTIVITIES</h2>
  <div class="abs calendar">
    <div class="cal-head"><span>«</span><span>JANUARY 2014</span><span>»</span></div>
    <div class="cal-grid">
      <div class="dow">Su</div><div class="dow">Mo</div><div class="dow">Tu</div><div class="dow">We</div><div class="dow">Th</div><div class="dow">Fr</div><div class="dow">Sa</div>
      <div class="mute">25</div><div class="mute">26</div><div class="mute">27</div><div class="mute">28</div><div class="mute">29</div><div class="mute">30</div><div>1</div>
      <div>2</div><div>3</div><div>4</div><div>5</div><div>6</div><div>7</div><div>8</div>
      <div>9</div><div>10</div><div>11</div><div>12</div><div>13</div><div class="bold">14</div><div>15</div>
      <div>16</div><div>17</div><div>18</div><div>19</div><div>20</div><div class="now">21</div><div>22</div>
      <div>23</div><div>24</div><div>25</div><div>26</div><div>27</div><div>28</div><div>29</div>
      <div>30</div><div class="mute">1</div><div class="mute">2</div><div class="mute">3</div><div class="mute">4</div><div class="mute">5</div><div class="mute">6</div>
    </div>
  </div>
  <div class="abs activity">
    <div class="activity-img" role="img" aria-label="Women exercising on treadmills"></div>
    <div>
      <div class="activity-date">Janu-24-2014</div>
      <p class="activity-text">Lorem ipsum dolor sit amet, consectetur adipisicing elit. Dicta ducimus numquam nu Lorem vulputat paentra</p>
    </div>
  </div>
  <div class="abs divider" style="top:926px"></div>
  <div class="abs cardio-title">Cardio Fitness</div>
  <div class="abs cardio-sub">Cardiovascular fitness</div>
  <svg class="abs" style="left:629px;top:941px" width="18" height="10" viewBox="0 0 18 10"><path d="M1 1l8 7 8-7" stroke="#aaa" stroke-width="1.5" fill="none"/></svg>
  <div class="abs divider" style="top:969px"></div>
</aside>

<footer>
  <div class="abs footer"></div>
  <div class="abs f-title" style="left:80px;top:1025px">Pixroll Photostream</div>
  <div class="abs thumbs" role="img" aria-label="Six small gym photos">
    <span></span><span></span><span></span><span></span><span></span><span></span>
  </div>

  <div class="abs f-title" style="left:249px;top:1025px">Latest Chirps</div>
  <div class="abs f-list" style="left:249px;top:1051px;width:120px">
    <div class="f-item"><i></i><div>Lorem Ipsum dolor sit Lorem rem Ipsum dolo.......<br>13-11-2-2013</div></div>
    <div class="f-item"><i></i><div>Lorem Ipsum dolor sit Lorem rem Ipsum dolo.......<br>13-11-2-2013</div></div>
  </div>

  <div class="abs f-title" style="left:399px;top:1025px">Contact Us</div>
  <div class="abs f-list" style="left:399px;top:1053px;width:120px;line-height:15px">
    <div class="f-item" style="margin-bottom:0"><i></i><div>Unit 12 Harbor Lane,<br>Eastvale 3040</div></div>
    <div class="f-item" style="margin-bottom:0"><i></i><div>02 5550 1188</div></div>
    <div class="f-item" style="margin-bottom:0"><i></i><div>hello@ironhouseclub.com</div></div>
  </div>

  <div class="abs f-title" style="left:543px;top:1026px">Newsletter</div>
  <div class="abs email">Enter your email..</div>
  <div class="abs subscribe">SUBSCRIBE</div>
  <div class="abs f-social">
    <span style="background:#39a9dc" aria-label="chirplo"></span>
    <span style="background:#3b5a9a" aria-label="kinwall"></span>
    <span style="background:#1f7bb6" aria-label="Worklink"></span>
    <span style="background:#e8e8e8" aria-label="Pixroll"></span>
    <span style="background:#cfcfcf" aria-label="Savestack"></span>
  </div>
  <div class="abs copy">Copyright © 2014 all rights are reserved</div>
</footer>

</body>
</html>
```